Web design for financial services

A modern web design of financial services (brokerage firm)
Req.s and technology tags :
- Very mobile friendly.
- One paged with some inner pages.
- Animated sticky header .
- Member login area for e-trade.
- Support RTL language.
- HTML & CSS.

The logo will be Home link
• MPTR :
WHO WE ARE
Content :
i) Board of Directors
ii) Mission Statement
iii) Corporate Values
iv) Regulations
• Financial Services :
WHAT WE DO
Content:
i) Electronic trading
ii) Trading desk
iii) Institutional
iv) Investors Education
• News
• Market Tools
• Forms---- opens new page
• Careers---- opens new page
• Contact Us----opens new page

The website is :
http://www.mptr-doha-example.com/

The logo need some changes to be more modern and impressively , but with keeping same structure .

Some related websites :
https://www.lv-bourse.example/

financial market

Financial Service

Coded - Design and coding required

2 page

• same fonts of http://www.kwdholdings.example/

• - Very mobile friendly.
• - One paged with some inner pages.
• - Animated sticky header .
• - Member login area for e-trade.
• - Support RTL language.
• - HTML & CSS.
• Slider , some Qatari theme,
• i like the video inside the home page
• ex :http://www.kwdholdings.example/

```html
<!DOCTYPE html>
<html lang="en">
<head>
<meta charset="utf-8">
<title>MPTR — Contact Us</title>
<link rel="stylesheet" href="https://fonts.googleapis.com/css2?family=Open+Sans:ital,wght@0,400;0,600;0,700;0,800;1,400;1,600&display=swap">
<style>
:root{
  --brand:#922b2b;
  --brand-dark:#7a2020;
  --ink:#333;
  --ink-soft:#555;
  --muted:#888;
  --line:#dcdcdc;
  --field:#efefef;
  --box:#f1f1f1;
  --footer:#000;
  --white:#fff;
  --map:#e4e4e4;
}
*{box-sizing:border-box;margin:0;padding:0}
html,body{width:1200px;height:3005px;overflow:hidden}
body{position:relative;background:var(--white);font-family:"Open Sans",Arial,sans-serif;color:var(--ink)}
.abs{position:absolute}

/* header */
.site-header{position:absolute;left:0;top:0;width:1200px;height:120px;background:var(--white)}
.brand{position:absolute;left:76px;top:30px;display:flex;align-items:center;gap:14px;font-size:44px;font-weight:800;color:var(--ink);letter-spacing:1px}
.brand-dot{width:44px;height:44px;border-radius:50%;background:var(--brand)}
.etrade{position:absolute;left:924px;top:26px;width:104px;height:27px;background:var(--brand);color:var(--white);font-size:11px;font-weight:700;display:flex;align-items:center;justify-content:center;gap:6px;border-radius:2px;white-space:nowrap}
.lang{position:absolute;left:1034px;top:26px;width:88px;height:27px;border:1px solid #bbb;font-size:10px;font-weight:600;display:flex;align-items:center;justify-content:center;border-radius:2px}
.main-nav{position:absolute;top:81px;right:76px;display:flex;gap:37px;font-size:12.5px;font-weight:700;color:#111;white-space:nowrap}
.main-nav .active{color:var(--brand)}

/* hero */
.hero{position:absolute;left:0;top:120px;width:1200px;height:546px;background:linear-gradient(120deg,#2b2f36 0%,#50555c 45%,#3a3530 75%,#6a5a48 100%)}
.hero-title{position:absolute;left:0;top:295px;width:1200px;text-align:center;font-size:68px;font-weight:700;color:var(--white)}

/* details */
.section-label{font-size:15px;font-weight:700;color:var(--brand)}
.label-bar{width:48px;height:4px;background:#222}
.office-name{font-size:17px;font-style:italic;font-weight:600;color:var(--ink-soft);white-space:nowrap}
.office-place{font-size:16px;font-weight:600;color:var(--brand);white-space:nowrap}
.small{font-size:11.5px;color:var(--ink-soft);white-space:nowrap}
.hours-title{font-size:14.5px;font-weight:700;color:#222}
.dept{position:absolute;top:1122px;width:276px;height:160px;background:var(--box);border:1px solid var(--line);padding:26px 20px;overflow:hidden}
.dept h3{font-size:15px;font-weight:600;color:var(--brand);margin-bottom:14px;white-space:nowrap}
.dept p{font-size:10.5px;color:var(--ink-soft);margin-bottom:13px;white-space:nowrap;letter-spacing:-0.1px}

/* map */
.map{position:absolute;left:0;top:1388px;width:1200px;height:540px;background:linear-gradient(180deg,#ececec,var(--map))}

/* form */
.form-title{font-size:20px;font-weight:700;color:var(--brand)}
.mandatory{font-size:11px;font-style:italic;color:var(--muted)}
.rule{height:1px;background:var(--line)}
.field-label{font-size:11.5px;color:var(--ink-soft);white-space:nowrap}
.field-label b{color:var(--brand);font-weight:600}
.field{position:absolute;height:37px;background:var(--field);border:1px solid #e2e2e2;font-size:11px;color:#444;display:flex;align-items:center;padding-left:10px}
.robot-check{position:absolute;left:160px;top:2252px;width:236px;height:70px;background:#f9f9f9;border:1px solid #d3d3d3;border-radius:3px;display:flex;align-items:center;padding-left:14px;gap:12px;font-size:12px}
.robot-check span{width:22px;height:22px;border:2px solid #c1c1c1;background:var(--white);border-radius:2px}
.send{position:absolute;left:160px;top:2338px;width:78px;height:40px;background:var(--brand);color:var(--white);font-size:13px;font-weight:700;display:flex;align-items:center;justify-content:center}

/* skyline + footer */
.skyline{position:absolute;left:0;top:2420px;width:1200px;height:326px;background:linear-gradient(180deg,#fff 0%,#e7c5c2 40%,#b8625c 100%)}
.site-footer{position:absolute;left:0;top:2746px;width:1200px;height:259px;background:var(--footer);color:var(--white)}
.footer-brand{position:absolute;left:0;top:56px;width:1200px;display:flex;justify-content:center;align-items:center;gap:10px;font-size:28px;font-weight:800}
.footer-brand i{width:26px;height:26px;border-radius:50%;border:2px solid var(--white)}
.footer-nav{position:absolute;left:0;top:128px;width:1200px;text-align:center;font-size:12.5px;font-weight:700;word-spacing:2px}
.copyright{position:absolute;left:0;top:160px;width:1200px;text-align:center;font-size:10.5px;color:#bbb}
.social{position:absolute;left:0;top:194px;width:1200px;display:flex;justify-content:center;gap:8px}
.social span{width:22px;height:22px;border-radius:50%;border:1.5px solid var(--white)}
</style>
</head>
<body>

<header class="site-header">
  <div class="brand"><span class="brand-dot"></span>MPTR</div>
  <div class="etrade">
    <svg width="10" height="10" viewBox="0 0 10 10"><rect x="1" y="1" width="8" height="8" fill="none" stroke="#fff" stroke-width="1.4"/></svg>MPTR E-TRADE</div>
  <div class="lang">ENGLISH&nbsp;&nbsp;⌄</div>
  <nav class="main-nav">
    <span>MPTR</span><span>FINANCIAL SERVICE</span><span>NEWS</span><span>MARKET TOOL</span><span>FORMS</span><span>CAREERS</span><span class="active">CONTACT US</span>
  </nav>
</header>

<section class="hero" role="img" aria-label="Photo of a trader reviewing printed charts next to a laptop on a desk">
  <h1 class="hero-title">CONTACT US</h1>
</section>
<svg class="abs" style="left:0;top:515px" width="1200" height="152" viewBox="0 0 1200 152"><polygon points="0,86 380,5 1200,150 1200,152 0,152" fill="#fff"/></svg>

<section class="contact-details">
  <div class="abs section-label" style="left:160px;top:700px">CONTACT DETAILS</div>
  <div class="abs label-bar" style="left:160px;top:734px"></div>

  <div class="abs office-name" style="left:160px;top:760px">Meridian Pearl Trading &amp; Research</div>
  <div class="abs office-place" style="left:160px;top:806px">Al Waha Complex</div>
  <div class="abs small" style="left:160px;top:838px">First Floor, Palm Junction</div>
  <div class="abs small" style="left:160px;top:866px">Tel: +974 40001234</div>
  <div class="abs small" style="left:160px;top:894px">Fax: +974 40005678</div>
  <div class="abs small" style="left:160px;top:914px">Email: recruitment@mptr-doha-example.com</div>

  <div class="abs office-name" style="left:476px;top:760px">Meridian Pearl Trading &amp; Research</div>
  <div class="abs office-place" style="left:476px;top:806px">Doha Bourse Branch</div>
  <div class="abs small" style="left:476px;top:838px">First Floor, Al Noor Tower,West Bay-in front of Harbour Center</div>
  <div class="abs small" style="left:476px;top:866px">Tel: +974 40002345</div>
  <div class="abs small" style="left:476px;top:894px">Fax: +974 40006789</div>
  <div class="abs small" style="left:476px;top:914px">Email: recruitment@mptr-doha-example.com</div>

  <div class="abs hours-title" style="left:160px;top:982px">WORKING HOURS</div>
  <div class="abs small" style="left:160px;top:1022px">Sunday - Thursday</div>
  <div class="abs small" style="left:286px;top:1022px">From 8:00 AM - 3:00 PM</div>
  <div class="abs small" style="left:160px;top:1046px">Friday and Saturday are officail holiday</div>

  <div class="abs hours-title" style="left:476px;top:982px">TRADING HOURS</div>
  <div class="abs small" style="left:476px;top:1022px">Sunday - Thursday</div>
  <div class="abs small" style="left:626px;top:1022px">Pre-Open: 9:00 AM</div>
  <div class="abs small" style="left:476px;top:1046px">Market Open: 9:30 AM</div>
  <div class="abs small" style="left:630px;top:1046px">Pre-Close: 1:00 PM</div>
  <div class="abs small" style="left:776px;top:1046px">Market Close: 1:15 PM</div>

  <div class="dept" style="left:160px"><h3>Call Centre Team</h3><p>Tel: +974 40001234</p><p>Fax: +974 40005678</p><p>Email: recruitment@mptr-doha-example.com</p></div>
  <div class="dept" style="left:460px"><h3>Communications Department</h3><p>Tel: +974 40001234</p><p>Fax: +974 40005678</p><p>Email: recruitment@mptr-doha-example.com</p></div>
  <div class="dept" style="left:760px"><h3>Compliance</h3><p>Tel: +974 40001234</p><p>Fax: +974 40005678</p><p>Email: recruitment@mptr-doha-example.com</p></div>
</section>

<section class="map" role="img" aria-label="Street map showing the office location"></section>
<svg class="abs" style="left:561px;top:1534px" width="62" height="106" viewBox="0 0 62 106"><path d="M31 0C14 0 0 14 0 31c0 24 31 75 31 75s31-51 31-75C62 14 48 0 31 0z" fill="#000"/><circle cx="31" cy="31" r="13" fill="none" stroke="#fff" stroke-width="4"/></svg>
<svg class="abs" style="left:0;top:1764px" width="1200" height="166" viewBox="0 0 1200 166"><polygon points="0,80 380,0 1200,162 1200,166 0,166" fill="#fff"/></svg>

<section class="contact-form">
  <div class="abs form-title" style="left:160px;top:1946px">CONTACT US</div>
  <div class="abs mandatory" style="right:164px;top:1954px">* mandatory fields</div>
  <div class="abs rule" style="left:160px;top:1990px;width:876px"></div>

  <div class="abs field-label" style="left:160px;top:2014px">Title <b>*</b></div>
  <div class="field" style="left:160px;top:2038px;width:254px">Choose one<svg style="position:absolute;right:12px" width="10" height="6"><polygon points="0,0 10,0 5,6" fill="#222"/></svg></div>
  <div class="abs field-label" style="left:430px;top:2014px">First Name <b>*</b></div>
  <div class="field" style="left:430px;top:2038px;width:254px"></div>
  <div class="abs field-label" style="left:702px;top:2014px">Message <b>*</b></div>
  <div class="field" style="left:702px;top:2038px;width:334px;height:190px"></div>

  <div class="abs field-label" style="left:160px;top:2089px">Last Name <b>*</b></div>
  <div class="field" style="left:160px;top:2112px;width:254px"></div>
  <div class="abs field-label" style="left:430px;top:2089px">Email <b>*</b></div>
  <div class="field" style="left:430px;top:2112px;width:254px"></div>

  <div class="abs field-label" style="left:160px;top:2166px">Country</div>
  <div class="field" style="left:160px;top:2190px;width:254px">Choose one<svg style="position:absolute;right:12px" width="10" height="6"><polygon points="0,0 10,0 5,6" fill="#222"/></svg></div>
  <div class="abs field-label" style="left:430px;top:2166px">Phone (including your country code) <b>*</b></div>
  <div class="abs field-label" style="left:432px;top:2200px;font-size:14px">+</div>
  <div class="field" style="left:452px;top:2190px;width:68px;color:#999">XXX</div>
  <div class="field" style="left:528px;top:2190px;width:156px"></div>

  <div class="robot-check"><span></span>I'm not a robot</div>
  <div class="send">SEND</div>
</section>

<section class="skyline" role="img" aria-label="Illustration of the Doha city skyline in red tones"></section>

<footer class="site-footer">
  <div class="footer-brand"><i></i>MPTR</div>
  <div class="footer-nav">MPTR &nbsp;|&nbsp; FINACIAL SERVICE &nbsp;|&nbsp; NEWS &nbsp;|&nbsp; MARKET TOOL &nbsp;|&nbsp; CAREERS &nbsp;|&nbsp; CONTACT US</div>
  <div class="copyright">©2017. All Rights Reserved | MPTR Qatar | Copyright, Legal and Privacy Statement,Disclaimers and Legal Information</div>
  <div class="social"><span></span><span></span><span></span><span></span><span></span></div>
</footer>

</body>
</html>
```